Card Design for my dog training business Brightpaw Obedience

Need a business card design for my dog training business with my new logo. Want the card to come off professional yet fun. Want it to be very eye catchy as well. I normally have these at vet clinics, pet stores, and groomers. so need it to look better than my competitors.
Target Market(s)
dog owners
Industry/Entity Type
Dog Training
Contact Information for Business Card
needs logo, my name and info
Font styles to use
Serif
Colors
0255a3
ffffff
ec1f27
000000
333333
fbfbfb
Requirements
Must have
- Brightpaw Obedience
- Felix Orland
- 415 903 2276
- info@brightpawobedience.example
- www.brightpawobedience.example

```html
<!DOCTYPE html>
<html lang="en">
<head>
<meta charset="utf-8">
<title>Brightpaw Obedience – Business Card</title>
<link rel="stylesheet" href="https://fonts.googleapis.com/css2?family=Noto+Serif:wght@400;700&family=EB+Garamond:ital@1&display=swap">
<style>
  :root {
    --stage: #2e2e2e;
    --card: #1c1c1e;
    --silver: #c9c9c9;
    --soft: #a9a9a9;
    --blue: #1f8ad6;
    --white: #fbfbfb;
  }
  * { box-sizing: border-box; margin: 0; padding: 0; }
  html, body { width: 799px; height: 1200px; overflow: hidden; }
  body {
    background: var(--stage);
    font-family: "Noto Serif", Georgia, serif;
    display: flex;
    flex-direction: column;
    align-items: center;
    justify-content: space-around;
    padding: 90px 0;
  }
  .card {
    position: relative;
    width: 660px;
    height: 378px;
    background: var(--card);
    border-radius: 4px;
    box-shadow: 0 18px 40px rgba(0,0,0,.45);
  }
  .card-front {
    display: flex;
    flex-direction: column;
    align-items: center;
    justify-content: center;
    gap: 30px;
  }
  .brand {
    display: flex;
    align-items: center;
    gap: 12px;
    color: var(--silver);
    font-weight: 700;
  }
  .brand-mark {
    width: 18px; height: 18px;
    background: var(--silver);
  }
  .card-front .brand-name { font-size: 34px; }
  .tagline {
    font-family: "EB Garamond", Georgia, serif;
    font-style: italic;
    font-size: 19px;
    color: var(--soft);
  }
  .card-back .brand {
    position: absolute;
    right: 40px;
    top: 110px;
  }
  .card-back .brand-name { font-size: 22px; }
  .identity {
    position: absolute;
    left: 40px;
    bottom: 120px;
    display: flex;
    align-items: baseline;
    gap: 12px;
  }
  .person-name { font-size: 28px; color: var(--blue); font-weight: 400; }
  .divider { font-size: 26px; color: var(--blue); }
  .role { font-size: 15px; color: var(--silver); }
  .contacts {
    position: absolute;
    left: 40px;
    bottom: 60px;
    right: 30px;
    display: flex;
    flex-wrap: wrap;
    gap: 8px 20px;
    list-style: none;
    font-size: 14px;
    color: var(--silver);
  }
  .contacts li { display: flex; align-items: center; gap: 7px; }
  .contacts svg { width: 14px; height: 14px; fill: var(--blue); }
</style>
</head>
<body>
  <section class="card card-front" aria-label="Card front">
    <div class="brand">
      <span class="brand-mark"></span>
      <span class="brand-name">Brightpaw Obedience</span>
    </div>
    <p class="tagline">“Training dogs across Texas one dog at a time.”</p>
  </section>

  <section class="card card-back" aria-label="Card back">
    <div class="brand">
      <span class="brand-mark"></span>
      <span class="brand-name">Brightpaw Obedience</span>
    </div>
    <div class="identity">
      <h1 class="person-name">Felix Orland</h1>
      <span class="divider">|</span>
      <span class="role">Dog Trainer</span>
    </div>
    <ul class="contacts">
      <li>
        <svg viewBox="0 0 24 24"><path d="M6.6 10.8a15.1 15.1 0 0 0 6.6 6.6l2.2-2.2c.3-.3.7-.4 1-.2 1.1.4 2.3.6 3.6.6.6 0 1 .4 1 1V20c0 .6-.4 1-1 1A17 17 0 0 1 3 4c0-.6.4-1 1-1h3.5c.6 0 1 .4 1 1 0 1.3.2 2.5.6 3.6.1.3 0 .7-.2 1z"/></svg>
        415 903 2276
      </li>
      <li>
        <svg viewBox="0 0 24 24"><path d="M2 5h20v14H2zm2 2v.5l8 5 8-5V7z"/></svg>
        info@brightpawobedience.example
      </li>
      <li>
        <svg viewBox="0 0 24 24"><path d="M12 2a10 10 0 1 0 0 20 10 10 0 0 0 0-20zm0 2c.9 1.2 1.6 2.7 2 4h-4c.4-1.3 1.1-2.8 2-4zM4.3 14a8 8 0 0 1 0-4h3.4a16 16 0 0 0 0 4zm.8 2h3c.3 1.3.9 2.5 1.5 3.6A8 8 0 0 1 5.1 16zm3-8h-3a8 8 0 0 1 4.5-3.6C8.9 5.5 8.4 6.7 8.1 8zM12 20c-.9-1.2-1.6-2.7-2-4h4c-.4 1.3-1.1 2.8-2 4zm2.3-6H9.7a14 14 0 0 1 0-4h4.6a14 14 0 0 1 0 4zm.1 5.6c.6-1.1 1.2-2.3 1.5-3.6h3a8 8 0 0 1-4.5 3.6zm1.9-5.6a16 16 0 0 0 0-4h3.4a8 8 0 0 1 0 4zm-.4-6c-.3-1.3-.9-2.5-1.5-3.6A8 8 0 0 1 18.9 8z"/></svg>
        www.brightpawobedience.example
      </li>
    </ul>
  </section>
</body>
</html>
```